Create a memorable Stationary for Security Software Company

Velbrantix is the worldwide leader in securing the Internet. Making Internet communications and critical data secure, reliable and available everywhere has been and continues to be our ongoing vision. We are committed to staying focused on real customer needs and to developing new and innovative security solutions that redefine the security landscape.

Industry/Entity Type

Internet

Font styles to use
Serif
Sans Serif
Script

Colors
0792cd
33a6d7
85cae6

```html
<!DOCTYPE html>
<html lang="en">
<head>
<meta charset="utf-8">
<title>Velbrantix Stationery</title>
<link href="https://fonts.googleapis.com/css2?family=Open+Sans:wght@400;600;700&display=swap" rel="stylesheet">
<style>
  :root {
    --blue: #0792cd;
    --blue-mid: #33a6d7;
    --blue-light: #85cae6;
    --white: #ffffff;
    --page: #eef1f3;
  }
  * { box-sizing: border-box; margin: 0; padding: 0; }
  html, body { width: 1200px; height: 1120px; overflow: hidden; }
  body {
    background: var(--page);
    font-family: "Open Sans", Arial, sans-serif;
    position: relative;
  }
  .card {
    position: absolute;
    left: 160px;
    width: 880px;
    height: 503px;
    box-shadow: 0 6px 18px rgba(0,0,0,0.18);
    overflow: hidden;
  }
  .card-front { top: 35px; background: var(--blue); }
  .card-back { top: 582px; background: var(--white); }

  .brand {
    position: absolute;
    display: flex;
    align-items: center;
    gap: 18px;
    font-weight: 700;
  }
  .brand-dot { border-radius: 50%; flex: none; }
  .card-front .brand {
    left: 0; right: 0; top: 170px; justify-content: center;
    color: var(--blue-light); font-size: 64px;
  }
  .card-front .brand-dot { width: 56px; height: 56px; background: var(--blue-light); }
  .front-url {
    position: absolute; left: 0; right: 0; top: 372px;
    text-align: center; color: var(--white);
    font-size: 27px; letter-spacing: 5px;
  }

  .card-back .brand {
    left: 50px; top: 220px; color: var(--blue-mid); font-size: 46px; gap: 12px;
  }
  .card-back .brand-dot { width: 40px; height: 40px; background: var(--blue-mid); }
  .back-divider { position: absolute; left: 0; top: 0; width: 880px; height: 503px; }
  .contact-panel {
    position: absolute; left: 470px; top: 0; right: 0; bottom: 0;
    color: var(--white); padding: 90px 0 0 40px;
  }
  .person-name { font-size: 30px; font-weight: 700; line-height: 1.2; }
  .person-title { font-size: 26px; margin-left: 8px; margin-bottom: 34px; }
  .contact-list { list-style: none; padding-left: 20px; }
  .contact-list li {
    display: flex; align-items: center; gap: 12px;
    font-size: 22px; line-height: 36px;
  }
  .contact-list svg { width: 20px; height: 20px; flex: none; }
  .contact-list .address { margin-top: 20px; align-items: flex-start; line-height: 30px; }
  .contact-list .address svg { margin-top: 6px; }
</style>
</head>
<body>
  <section class="card card-front">
    <div class="brand"><span class="brand-dot"></span>Velbrantix</div>
    <div class="front-url">www.velbrantix.com</div>
  </section>

  <section class="card card-back">
    <svg class="back-divider" viewBox="0 0 880 503" aria-hidden="true">
      <path d="M470 0 H880 V503 H470 V118 L456 108 L470 98 Z" fill="#0792cd"/>
      <path d="M455 0 V96 L442 108 L455 120 V503" fill="none" stroke="#0792cd" stroke-width="5"/>
    </svg>
    <div class="brand"><span class="brand-dot"></span>Velbrantix</div>

    <div class="contact-panel">
      <div class="person-name">Your Name</div>
      <div class="person-title">Title</div>
      <ul class="contact-list">
        <li>
          <svg viewBox="0 0 20 20"><circle cx="10" cy="10" r="9" fill="none" stroke="#fff" stroke-width="2"/><path d="M7 5 L9 8 L8 9 Q9 11 11 12 L12 11 L15 13 L13 15 Q8 14 5 7 Z" fill="#fff"/></svg>
          012-345-6789
        </li>
        <li>
          <svg viewBox="0 0 20 20"><rect x="5" y="1" width="10" height="18" rx="2" fill="#fff"/><rect x="7" y="4" width="6" height="6" fill="#0792cd"/></svg>
          012-345-6789
        </li>
        <li>
          <svg viewBox="0 0 20 20"><rect x="1" y="4" width="18" height="12" rx="1" fill="#fff"/><path d="M2 5 L10 11 L18 5" fill="none" stroke="#0792cd" stroke-width="2"/></svg>
          info@velbrantix.com
        </li>
        <li>
          <svg viewBox="0 0 20 20" fill="none" stroke="#fff" stroke-width="1.6"><circle cx="10" cy="10" r="8.5"/><ellipse cx="10" cy="10" rx="4" ry="8.5"/><path d="M1.5 10 H18.5 M3 5.5 H17 M3 14.5 H17"/></svg>
          www.velbrantix.com
        </li>
        <li class="address">
          <svg viewBox="0 0 20 20"><circle cx="10" cy="10" r="9" fill="#fff"/><path d="M10 4 A3.5 3.5 0 0 1 13.5 7.5 Q13.5 10 10 15 Q6.5 10 6.5 7.5 A3.5 3.5 0 0 1 10 4 Z" fill="#0792cd"/></svg>
          <span>Street Name, City Name<br>Zipcode-012345</span>
        </li>
      </ul>
    </div>
  </section>
</body>
</html>
```